Professional & attention grabbing.

A business card design, front and back. I already have a logo I will attach, but I am open to something new as well.
Things to include:
Name:
Title:
Phone:
Email:
Wanting something that is professional but attention grabbing.
Also we do a lot of work using drones on natural gas pipelines (leading the future)if you want to include any of that. I'm open to ideas.
Target Market(s)
Natural gas transmission industry / greenhouse gas mitigation industry
Industry/Entity Type
Business
Colors
Designer to choose colors to be used in the design.
Look and feel
Each slider illustrates characteristics of the customer's brand and the style your logo design should communicate.

```html
<!DOCTYPE html>
<html lang="en">
<head>
<meta charset="UTF-8">
<title>Kestrel Inspections — Business Card</title>
<link href="https://fonts.googleapis.com/css2?family=Exo+2:wght@400;600;700&display=swap" rel="stylesheet">
<style>
  :root {
    --backdrop: #4a4a4a;
    --card-white: #fdfdfd;
    --brand-red: #c0161f;
    --ink-dark: #2f2f31;
    --ink-body: #333336;
    --rule: #c9a9ab;
    --band: #ecefee;
  }
  * { margin: 0; padding: 0; box-sizing: border-box; }
  html, body {
    width: 1200px; height: 900px; overflow: hidden;
    background: var(--backdrop);
    font-family: "Exo 2", Arial, sans-serif;
  }
  .canvas { position: relative; width: 1200px; height: 900px; }
  .card {
    position: absolute; top: 271px;
    width: 457px; height: 282px;
    border-radius: 14px; overflow: hidden;
    box-shadow: 3px 4px 6px rgba(0,0,0,0.45);
  }
  .card-front { left: 137px; background: var(--card-white); }
  .card-back { left: 626px; background: #8fb6cc; }

  /* front */
  .brand {
    position: absolute; left: 36px; top: 106px;
    display: flex; align-items: center; gap: 10px;
  }
  .brand-mark { width: 22px; height: 22px; background: var(--brand-red); }
  .brand-name {
    font-weight: 700; font-size: 21px; line-height: 1.05;
    color: var(--ink-dark); letter-spacing: 0.3px;
  }
  .divider {
    position: absolute; left: 244px; top: 76px;
    width: 1px; height: 128px; background: var(--rule);
  }
  .contact { position: absolute; left: 261px; top: 72px; color: var(--ink-body); }
  .person-name {
    font-weight: 700; font-size: 19px; color: var(--brand-red);
    letter-spacing: 0.4px; line-height: 22px;
  }
  .person-title { font-weight: 600; font-size: 12.5px; letter-spacing: 0.5px; line-height: 14px; }
  .contact-list { list-style: none; margin-top: 19px; font-size: 13px; }
  .contact-list li { display: flex; align-items: center; gap: 7px; height: 21px; }
  .icon {
    width: 12px; height: 12px; background: var(--brand-red); border-radius: 2px;
    display: flex; align-items: center; justify-content: center;
  }
  .address { margin-top: 6px; font-size: 13px; line-height: 17px; }

  /* back */
  .photo { position: absolute; }
  .photo-pipeline {
    left: 0; top: 0; width: 226px; height: 157px;
    background: linear-gradient(180deg, #d8b79a 0%, #c8a58c 45%, #7d7f86 70%, #6d7178 100%);
  }
  .photo-site {
    left: 229px; top: 0; width: 228px; height: 157px;
    background: linear-gradient(180deg, #bcd0e4 0%, #dfe6ee 50%, #9d9384 78%, #7f7568 100%);
  }
  .photo-landscape {
    left: 0; top: 159px; width: 457px; height: 123px;
    background: linear-gradient(180deg, #cfe3ee 0%, #5aa3c8 30%, #3d8fb7 60%, #6e9d8c 100%);
  }
  .web-band {
    position: absolute; left: 0; top: 239px; width: 457px; height: 18px;
    background: var(--band);
    display: flex; align-items: center; justify-content: center;
  }
  .web-address { font-size: 13px; font-weight: 600; color: var(--brand-red); letter-spacing: 0.2px; }
  .back-brand {
    position: absolute; left: 146px; top: 122px;
    display: flex; align-items: center; gap: 8px;
  }
  .back-brand .brand-mark { width: 20px; height: 20px; }
  .back-brand .brand-name { color: var(--brand-red); font-size: 22px; }
</style>
</head>
<body>
<main class="canvas">
  <section class="card card-front" aria-label="Business card front">
    <div class="brand">
      <span class="brand-mark"></span>
      <span class="brand-name">Kestrel<br>Inspections</span>
    </div>
    <div class="divider"></div>
    <div class="contact">
      <p class="person-name">DANIEL WARD</p>
      <p class="person-title">DIRECTOR</p>
      <ul class="contact-list">
        <li>
          <span class="icon"><svg width="8" height="8" viewBox="0 0 8 8"><path d="M1.5 0.8 L3 2.3 L2.2 3.2 Q3.3 5 4.8 5.8 L5.7 5 L7.2 6.5 L6.3 7.4 Q3 6.5 0.6 1.7 Z" fill="#fff"/></svg></span>
          555-210-4870
        </li>
        <li>
          <span class="icon"><svg width="8" height="6" viewBox="0 0 8 6"><rect x="0.5" y="0.5" width="7" height="5" fill="none" stroke="#fff"/><path d="M0.5 0.5 L4 3.3 L7.5 0.5" fill="none" stroke="#fff"/></svg></span>
          hello@kestrel-inspect.com
        </li>
      </ul>
      <p class="address">48 Harbor Line Road,<br>Westfield Park, Tokyo</p>
    </div>
  </section>

  <section class="card card-back" aria-label="Business card back">
    <div class="photo photo-pipeline" role="img" aria-label="Photo of a drone flying beside a gas pipeline at an industrial site at dusk"></div>
    <div class="photo photo-site" role="img" aria-label="Photo of a drone over a pipeline construction site with cranes"></div>
    <div class="photo photo-landscape" role="img" aria-label="Photo of drones over blue mountains and a pipeline crossing green plains"></div>
    <div class="web-band"><span class="web-address">www.kestrel-inspect.com</span></div>
    <div class="back-brand">
      <span class="brand-mark"></span>
      <span class="brand-name">Kestrel Inspections</span>
    </div>
  </section>
</main>
</body>
</html>
```